QRV Advisors needs a web site

We need a web site for www.qrvadvisors-example.com. QRV is a mergers and acquisition consulting company that focuses our buyer and seller services on logistics companies. We help put companies together, and help with legal and financial due diligence. We want the web site to express our service and show the logistics components. We want personalized images versus pictures of trucks and airplanes.

Our new logo uses Burgandy and grey colors. Image attached. We are not in to bold, big letters...classy, artistic, low key preferred. Confidentiality, experience, professional are what we want to express on the site.

All we expect for the first part of this project is a home page, and one subpage.  We are budgeting other funds for the technical aspects of the web site

Reason: All that I'm seeing so far is trucks, forklifts and planes. We are a legal mergers and acquisitions firm that focus on logistics. I like some of the images to say logistics, but really want it say legal, financial, and putting companies together. Will pay extra for the sub page if someone can impress us with a home page.

Reason: Swamped with another project at the moment...will work on this over the weekend and provide designer feedback and select final design by Tuesday

```html
<!DOCTYPE html>
<html lang="en">
<head>
<meta charset="utf-8">
<title>QRV Advisors</title>
<link rel="stylesheet" href="https://fonts.googleapis.com/css2?family=Ubuntu:wght@400;500;700&family=Roboto:wght@400;500;700&display=swap">
<style>
:root{
  --burgundy:#a50d34;
  --burgundy-dark:#8f0a2c;
  --charcoal:#333333;
  --text:#3d3d3d;
  --muted:#6a6a6a;
  --line:#d6d6d6;
  --panel:#f4f4f4;
  --white:#ffffff;
}
*{box-sizing:border-box;margin:0;padding:0}
html,body{width:1069px;height:1200px;overflow:hidden;background:var(--white)}
body{font-family:"Ubuntu",sans-serif;color:var(--text);position:relative}
.site{position:relative;width:1069px;height:1200px;overflow:hidden;background:#fafafa}

/* header */
.site-header{position:absolute;left:0;top:0;width:1069px;height:94px;background:linear-gradient(#ffffff,#efefef)}
.brand{position:absolute;left:110px;top:22px;display:flex;align-items:center;gap:10px}
.brand-mark{width:14px;height:14px;background:var(--burgundy)}
.brand-name{font-family:"Ubuntu",sans-serif;font-size:34px;font-weight:400;color:var(--burgundy);letter-spacing:1px}
.phone{position:absolute;right:117px;top:34px;display:flex;align-items:center;gap:10px;font-size:21px;color:var(--burgundy)}

/* nav */
.main-nav{position:absolute;left:0;top:94px;width:1069px;height:45px;background:var(--charcoal);border-bottom:1px solid #222}
.main-nav ul{list-style:none;display:flex;position:absolute;left:113px;top:0;height:45px}
.main-nav li{height:45px;display:flex;align-items:center;justify-content:center;font-size:15.5px;color:#fff;border-right:1px solid #4a4a4a;white-space:nowrap}
.main-nav li.active{background:#fff;color:var(--burgundy)}
.main-nav li:last-child{border-right:none}
.search{position:absolute;left:753px;top:8px;width:196px;height:25px;background:#9a9a9a;color:#eee;font-size:12.5px;padding:5px 9px}
.search svg{position:absolute;right:7px;top:5px}

/* hero */
.hero{position:absolute;left:0;top:139px;width:1069px;height:414px;background:linear-gradient(120deg,#6f7fb0 0%,#8a98c6 35%,#c7b3bd 60%,#4b5b8e 100%)}
.hero-caption{position:absolute;left:0;bottom:0;width:100%;height:43px;background:rgba(40,40,40,.82);color:#fff;font-size:19.5px;padding:9px 0 0 120px}
.dots{position:absolute;right:120px;top:17px;display:flex;gap:8px}
.dots span{width:10px;height:10px;border-radius:50%;background:#fff}
.dots span.on{background:var(--burgundy)}

/* services */
.services{position:absolute;left:277px;top:547px;width:514px;height:76px;background:linear-gradient(#fdfdfd,#e6e6e6);border-radius:0 0 6px 6px;box-shadow:0 3px 6px rgba(0,0,0,.2);display:flex}
.service{flex:1;display:flex;align-items:center;gap:8px;padding-left:10px;border-right:1px solid var(--line);color:var(--burgundy);font-size:15.5px;font-weight:500;line-height:18px}
.service:last-child{border-right:none}

/* cards */
.card{position:absolute;top:667px;width:269px;height:273px;background:var(--panel);border:1px solid var(--line)}
.card-title{position:absolute;left:50%;top:-5px;transform:translateX(-50%);width:170px;height:29px;background:var(--burgundy);color:#fff;font-family:"Roboto",sans-serif;font-weight:500;font-size:15.5px;text-align:center;line-height:29px;border-radius:2px}
.btn{position:absolute;bottom:-4px;right:14px;background:var(--charcoal);color:#fff;font-family:"Roboto",sans-serif;font-size:11.5px;padding:3px 7px;border-radius:3px 3px 0 0}
.mission-photo{position:absolute;left:10px;top:43px;width:247px;height:86px;border:4px solid #fff;outline:1px solid var(--line);background:linear-gradient(90deg,#6b5a4f,#d9c6b0 40%,#bfa892 70%,#4e4a4c)}
.mission-text{position:absolute;left:15px;top:141px;width:240px;font-family:"Roboto",sans-serif;font-size:11.2px;line-height:16.6px;color:#444}
.news-item{position:absolute;left:12px;width:244px;display:flex;gap:12px}
.news-item+.news-item{border-top:1px solid var(--line)}
.date{width:31px;flex:none;text-align:center;font-family:"Roboto",sans-serif}
.date .m{background:#4a4a4a;color:#fff;font-size:10.5px;padding:1px 0}
.date .d{background:#ddd;color:#444;font-size:15px;padding:1px 0}
.news-body{font-family:"Roboto",sans-serif;font-size:10.6px;line-height:15px;color:#444}
.news-body strong{display:block;font-weight:500;font-size:12px;margin-bottom:1px}
.form-row{position:absolute;left:17px;font-family:"Roboto",sans-serif;font-size:11.5px;color:#555}
.field{position:absolute;left:77px;width:170px;height:19px;background:#fff;border:1px solid #ccc}

/* partners */
.partners{position:absolute;left:0;top:967px;width:1069px;height:72px}
.partner{position:absolute;top:22px;display:flex;align-items:center;gap:6px;font-family:"Ubuntu",sans-serif;font-weight:500;font-size:23px;color:#4d4d4d}
.partner i{width:12px;height:12px;background:#4d4d4d;display:block}
.arrow{position:absolute;top:20px}

/* footer */
.site-footer{position:absolute;left:0;top:1049px;width:1069px;height:151px;background:var(--burgundy);color:#fff}
.site-footer h3{font-weight:400;font-size:16.5px;margin-bottom:10px}
.col{position:absolute;top:11px}
.col ul{list-style:none;font-family:"Roboto",sans-serif;font-size:12px;line-height:18px}
.col p{font-family:"Roboto",sans-serif;font-size:11px;line-height:15px;width:215px}
.email{margin-top:10px;width:184px;height:21px;background:#fff;color:#888;font-size:11px;padding:3px 9px;border-radius:2px;font-family:"Roboto",sans-serif}
.subscribe{margin-top:14px;display:inline-block;background:var(--charcoal);font-size:13px;padding:3px 7px;border-radius:3px}
.social{display:flex;align-items:center;gap:10px;font-family:"Roboto",sans-serif;font-size:12.5px;margin-bottom:12px}
.social i{width:22px;height:22px;border-radius:4px;background:#fff;opacity:.85;display:block}
.footer-brand{position:absolute;left:742px;top:28px;font-size:56px;letter-spacing:10px;font-weight:400}
.copyright{position:absolute;left:742px;top:108px;width:220px;text-align:center;font-family:"Roboto",sans-serif;font-size:11.5px;line-height:16px}
</style>
</head>
<body>
<div class="site">

  <header class="site-header">
    <div class="brand"><span class="brand-mark"></span><span class="brand-name">QRV Advisors</span></div>
    <div class="phone">
      <svg width="22" height="22" viewBox="0 0 22 22" aria-hidden="true"><circle cx="11" cy="11" r="10" fill="none" stroke="#777" stroke-width="1.5"/><path d="M8 6c-1 1-1 3 1 6s4 4 5 4l1-1-2-2-1 1c-1-.5-2.5-2-3-3l1-1-2-2z" fill="#777"/></svg>
      555 010 2030
    </div>
  </header>

  <nav class="main-nav">
    <ul>
      <li class="active" style="width:81px">Home</li>
      <li style="width:89px">About Us</li>
      <li style="width:166px">Consulting Services</li>
      <li style="width:129px">News &amp; Events</li>
      <li style="width:67px">FAQ's</li>
      <li style="width:96px">Contact Us</li>
    </ul>
    <div class="search">Search
      <svg width="14" height="14" viewBox="0 0 14 14" aria-hidden="true"><circle cx="6" cy="6" r="4.3" fill="none" stroke="#fff" stroke-width="2"/><path d="M9 9l4 4" stroke="#fff" stroke-width="2"/></svg>
    </div>
  </nav>

  <section class="hero" role="img" aria-label="Businessman touching a glowing virtual interface showing strategy, plan, investment, income and money">
    <div class="hero-caption">QRV Services Are Offered By Industry Executives With Extensive M&amp;A Experience
      <div class="dots"><span class="on"></span><span></span><span></span><span></span><span></span></div>
    </div>
  </section>

  <section class="services">
    <div class="service">
      <svg width="50" height="58" viewBox="0 0 50 58" aria-hidden="true"><rect x="4" y="8" width="30" height="44" fill="none" stroke="#5a5a5a" stroke-width="3"/><rect x="10" y="3" width="30" height="44" fill="#eee" stroke="#5a5a5a" stroke-width="3"/><path d="M15 13h20M15 20h20M15 27h20M15 34h12" stroke="#5a5a5a" stroke-width="2.5"/><path d="M28 42l6 6 12-14" fill="none" stroke="#5a5a5a" stroke-width="3"/></svg>
      <span>Bussiness<br>&amp; Planning</span>
    </div>
    <div class="service">
      <svg width="50" height="64" viewBox="0 0 50 64" aria-hidden="true"><path d="M25 2l-12 22h8c0 12-8 22-12 38h10c2-10 6-16 6-16s4 6 6 16h10c-4-16-12-26-12-38h8z" fill="#5a5a5a"/></svg>
      <span>Mergers<br>&amp; Acquisition</span>
    </div>
    <div class="service" style="gap:18px">
      <svg width="60" height="60" viewBox="0 0 60 60" aria-hidden="true"><circle cx="30" cy="30" r="26" fill="none" stroke="#5a5a5a" stroke-width="5"/><circle cx="30" cy="30" r="19" fill="none" stroke="#5a5a5a" stroke-width="1.5"/><path d="M36 18l6 6-14 14-8 2 2-8z" fill="none" stroke="#5a5a5a" stroke-width="2"/></svg>
      <span>Advisory<br>Services</span>
    </div>
  </section>

  <article class="card" style="left:110px">
    <div class="card-title">Our Mission</div>
    <div class="mission-photo" role="img" aria-label="Group of smiling business professionals"></div>
    <p class="mission-text">Lorem Ipsum is simply dummy text of the printing and typesetting industry. Lorem Ipsum has been the industry's standard dummy text ever since the 1500sstandard dummy text ever since the 1500s dustry. Lorem Idustry. Lorem I dustry. Lorem.,</p>
    <span class="btn">Read More</span>
  </article>

  <article class="card" style="left:400px">
    <div class="card-title">News &amp; Events</div>
    <div class="news-item" style="top:37px;padding-top:6px">
      <div class="date"><div class="m">APR</div><div class="d">02</div></div>
      <div class="news-body"><strong>Lorem ipsum dolor sit amet</strong>Lorem ipsum dol adipiscing elit, seder or sit amet, consectetu industry's standard dummy text ever er</div>
    </div>
    <div class="news-item" style="top:108px;padding-top:8px">
      <div class="date"><div class="m">APR</div><div class="d">02</div></div>
      <div class="news-body"><strong>Lorem ipsum dolor sit amet</strong>Lorem ipsum dol adipiscing elit, seder or sit amet, consectetu industry's standard dummy text ever er</div>
    </div>
    <div class="news-item" style="top:189px;padding-top:8px">
      <div class="date"><div class="m">APR</div><div class="d">02</div></div>
      <div class="news-body"><strong>Lorem ipsum dolor sit amet</strong>Lorem ipsum dol adipiscing elit, seder or sit amet, consectetu</div>
    </div>
    <span class="btn">Read More</span>
  </article>

  <article class="card" style="left:689px">
    <div class="card-title">Get in touch</div>
    <div class="form-row" style="top:50px">Name</div><div class="field" style="top:40px"></div>
    <div class="form-row" style="top:91px">Phone</div><div class="field" style="top:80px"></div>
    <div class="form-row" style="top:131px">Email</div><div class="field" style="top:120px"></div>
    <div class="form-row" style="top:171px">Message</div><div class="field" style="top:161px;height:62px"></div>
    <span class="btn" style="padding:3px 13px">Submit</span>
  </article>

  <section class="partners">
    <svg class="arrow" style="left:124px" width="18" height="30" viewBox="0 0 18 30" aria-hidden="true"><path d="M15 3L4 15l11 12" fill="none" stroke="#999" stroke-width="3"/></svg>
    <div class="partner" style="left:205px"><i></i>Norvane</div>
    <div class="partner" style="left:393px">Haulwise</div>
    <div class="partner" style="left:572px">Stridewell</div>
    <div class="partner" style="left:755px">Pathmere</div>
    <svg class="arrow" style="left:938px" width="18" height="30" viewBox="0 0 18 30" aria-hidden="true"><path d="M3 3l11 12L3 27" fill="none" stroke="#999" stroke-width="3"/></svg>
  </section>

  <footer class="site-footer">
    <div class="col" style="left:125px">
      <h3>Quick Links</h3>
      <ul><li>Home</li><li>About Us</li><li>Consulting Services</li><li>News &amp; Events</li><li>FAQ's</li><li>Contact Us</li></ul>
    </div>
    <div class="col" style="left:307px">
      <h3>Newsletter</h3>
      <p>Lorem Ipsum is simply dummy text of the printing and typesetting industry.</p>
      <div class="email">your e-mail address</div>
      <span class="subscribe">Subscribe</span>
    </div>
    <div class="col" style="left:579px">
      <h3>Follow Us</h3>
      <div class="social"><i></i>Friendbook</div>
      <div class="social"><i></i>Chirper</div>
      <div class="social"><i></i>Linkwork</div>
    </div>
    <div class="footer-brand">QRV</div>
    <div class="copyright">© 2014 QRV Advisors.<br>All Rights Reserved</div>
  </footer>

</div>
</body>
</html>
```